BrindleStaffing Business Card Design

We are a staffing company finding positions for dedicated nurses and physicians.

Target Market(s)

Business Professionals

Industry/Entity Type

Staffing

Contact Information for Business Card

Gordon Pratley
Chairman
417 39th Avenue South
SAINT PETERSBURG FL 33712
813-555-4172 Mobile
813-555-8036 Fax
gpratley@brindlestaffing.com
www.brindlestaffing.com

Font styles to use
Sans Serif

Colors
fbee3e
f04a50
f37122

Requirements
Must have
• Logo Attached, see colors below. We'd like to see Yellow, Orange and Red.

```html
<!DOCTYPE html>
<html lang="en">
<head>
<meta charset="utf-8">
<title>BrindleStaffing Business Card</title>
<link rel="stylesheet" href="https://fonts.googleapis.com/css2?family=Poppins:wght@600&family=Questrial&display=swap">
<style>
  :root {
    --page: #dedede;
    --card: #e8e8e8;
    --yellow: #fbee3e;
    --orange: #f37122;
    --red: #f04a50;
    --ink: #5b5b5b;
    --white: #ffffff;
  }
  * { margin: 0; padding: 0; box-sizing: border-box; }
  html, body { width: 1200px; height: 1200px; overflow: hidden; }
  body { background: var(--page); position: relative; font-family: "Questrial", sans-serif; }

  .card {
    position: absolute;
    left: 227px;
    width: 745px;
    height: 425px;
    border-radius: 38px;
    overflow: hidden;
  }
  .card--front { top: 135px; background: var(--card); }
  .card--back {
    top: 640px;
    background: linear-gradient(90deg, var(--yellow) 0%, #f7a62c 22%, var(--orange) 50%, #f15c3c 78%, var(--red) 100%);
  }

  .brand-name {
    position: absolute;
    font-family: "Poppins", sans-serif;
    font-weight: 600;
    letter-spacing: -1px;
    white-space: nowrap;
  }
  .card--front .brand-name {
    left: 34px; top: 178px;
    font-size: 48px;
    color: var(--orange);
  }
  .card--back .brand-name {
    left: 0; right: 0; top: 160px;
    text-align: center;
    font-size: 68px;
    color: var(--white);
  }

  .divider {
    position: absolute;
    left: 420px; top: 93px;
    width: 2px; height: 237px;
    background: linear-gradient(180deg, var(--red), var(--orange));
  }

  .details { position: absolute; left: 443px; top: 90px; color: var(--ink); }
  .person-name {
    font-family: "Poppins", sans-serif;
    font-weight: 600;
    font-size: 21px;
    line-height: 26px;
  }
  .person-name .first { color: var(--orange); }
  .person-name .last { color: var(--red); }
  .person-title { font-size: 17px; line-height: 22px; }
  .address { margin-top: 32px; font-size: 17px; line-height: 22px; }
  .contacts { margin-top: 36px; list-style: none; font-size: 17px; line-height: 22px; }
  .contacts li { display: flex; align-items: center; gap: 9px; }
  .contacts svg { width: 16px; height: 16px; flex: none; }
  .web .accent-a { color: var(--orange); }
  .web .accent-b { color: var(--red); }
</style>
</head>
<body>
  <section class="card card--front">
    <div class="brand-name">BrindleStaffing</div>
    <div class="divider"></div>
    <div class="details">
      <h1 class="person-name"><span class="first">Gordon</span> <span class="last">Pratley</span></h1>
      <p class="person-title">Chairman</p>
      <p class="address">417 39th Avenue South<br>SAINT PETERSBURG FL 33712</p>
      <ul class="contacts">
        <li>
          <svg viewBox="0 0 16 16" aria-hidden="true"><path fill="#f37122" d="M1 6c0-2 3-3 7-3s7 1 7 3v1h-3V5.5H4V7H1zM3 8l2-2h6l2 2v5H3z"/><circle cx="8" cy="10" r="1.6" fill="#e8e8e8"/></svg>
          <span>813-555-4172</span>
        </li>
        <li>
          <svg viewBox="0 0 16 16" aria-hidden="true"><rect x="2" y="1" width="3" height="14" rx="1" fill="#f37122"/><rect x="6" y="4" width="9" height="11" rx="1" fill="#f37122"/><rect x="7.5" y="1" width="6" height="4" fill="#f37122"/><rect x="7.5" y="6" width="6" height="3" fill="#e8e8e8"/></svg>
          <span>813-555-8036</span>
        </li>
        <li>
          <svg viewBox="0 0 16 16" aria-hidden="true"><rect x="1" y="3" width="14" height="10" fill="none" stroke="#f37122" stroke-width="1.6"/><path d="M1 3l7 6 7-6M1 13l5-5M15 13l-5-5" fill="none" stroke="#f37122" stroke-width="1.4"/></svg>
          <span>gpratley@brindlestaffing.com</span>
        </li>
        <li class="web">
          <svg viewBox="0 0 16 16" aria-hidden="true"><circle cx="8" cy="8" r="7" fill="#f37122"/><path d="M4 4c2 0 2 2 4 2s1 3-1 3-1 3-3 2zM10 10c1-1 3-1 3 1-1 1-2 1-3-1z" fill="#e8e8e8"/></svg>
          <span>www.<span class="accent-a">brindle</span><span class="accent-b">staffing</span>.com</span>
        </li>
      </ul>
    </div>
  </section>

  <section class="card card--back">
    <div class="brand-name">BrindleStaffing</div>
  </section>
</body>
</html>
```